Computer consultant business card

Bexil Software is a newly started computer consulting company. It's a small one-man company that provides mostly Vornix applications but also websites in collaboration with designers. I'm running this company on the side of full time university studies.

I want the final design to be clean and memorable. Be creative! :)

Some inspiration:
http://www.pixelmarta.com/design/48317
http://www.pixelmarta.com/design/2739164/business-card-design-by-frostlynk
http://www.pixelmarta.com/design/604281/business-card-design-by-koralind-vestrabanu

See attachment for my company logo.
Updates

I would like to thank everyone for submitting! I'll need a couple of days to review and ultimately select a design.

Target Market(s)

Non-technical entrepreneurs and small companies.

Industry/Entity Type

University

Requirements
Must have
• My company logo.
In any way, both colors from my logo.
First- and last name, e-mail and phone number.
Double-sided design.
Nice to have
• Something creative with the symbol in my logo

```html
<!DOCTYPE html>
<html lang="en">
<head>
<meta charset="utf-8">
<title>Bexil Software – Business Card</title>
<link rel="stylesheet" href="https://fonts.googleapis.com/css2?family=Exo+2:wght@400;600;700&display=swap">
<style>
  :root {
    --canvas-bg: #e9e6e2;
    --card-white: #ffffff;
    --brand-blue: #2178f0;
    --brand-blue-soft: #3f8bf3;
    --brand-dark: #2f2e30;
    --text-dark: #2b2b2d;
    --card-shadow: 0 10px 28px rgba(0, 0, 0, 0.28);
  }
  * { box-sizing: border-box; margin: 0; padding: 0; }
  html, body {
    width: 1200px;
    height: 820px;
    overflow: hidden;
    background: var(--canvas-bg);
    font-family: "Exo 2", sans-serif;
  }
  .canvas {
    position: relative;
    width: 1200px;
    height: 820px;
  }
  .card {
    position: absolute;
    width: 545px;
    height: 312px;
    overflow: hidden;
    box-shadow: var(--card-shadow);
  }

  /* ---------- Front ---------- */
  .card--front {
    left: 40px;
    top: 254px;
    background: var(--card-white);
  }
  .front-waves {
    position: absolute;
    inset: 0;
    width: 100%;
    height: 100%;
  }
  .brand {
    position: absolute;
    left: 56px;
    top: 56px;
    display: flex;
    align-items: center;
    gap: 18px;
  }
  .brand__dot {
    width: 62px;
    height: 62px;
    border-radius: 50%;
    background: var(--brand-blue);
  }
  .brand__name {
    font-size: 64px;
    font-weight: 700;
    line-height: 1;
    color: var(--brand-dark);
    letter-spacing: 1px;
  }
  .contact {
    position: absolute;
    left: 28px;
    top: 172px;
    color: var(--text-dark);
    font-size: 15px;
    line-height: 1;
  }
  .contact__address { margin-bottom: 24px; }
  .contact__row {
    display: flex;
    align-items: center;
    gap: 7px;
    margin-bottom: 7px;
  }
  .contact__row--phone { font-size: 17px; }
  .contact__icon {
    width: 12px;
    height: 12px;
    flex: none;
  }
  .person {
    position: absolute;
    right: 18px;
    top: 205px;
    text-align: right;
    color: var(--card-white);
    line-height: 1.15;
  }
  .person__first { font-size: 17px; font-weight: 700; }
  .person__last { font-size: 15px; font-weight: 400; padding-right: 2px; }

  /* ---------- Back ---------- */
  .card--back {
    left: 615px;
    top: 254px;
    background: var(--brand-blue);
  }
  .back-pattern {
    position: absolute;
    inset: 0;
    background: radial-gradient(ellipse at 50% 50%, var(--brand-blue) 35%, var(--brand-blue-soft) 100%);
  }
  .back-name {
    position: absolute;
    left: 0;
    right: 0;
    top: 50%;
    transform: translateY(-50%);
    text-align: center;
    font-size: 118px;
    font-weight: 700;
    line-height: 1;
    color: var(--card-white);
    letter-spacing: 2px;
  }
</style>
</head>
<body>
<main class="canvas">

  <section class="card card--front" aria-label="Business card front">
    <svg class="front-waves" viewBox="0 0 545 312" aria-hidden="true">
      <path d="M0,0 L70,0 C40,20 18,48 0,90 Z" fill="var(--brand-blue)"/>
      <path d="M86,0 C52,22 26,52 8,96" fill="none" stroke="var(--brand-dark)" stroke-width="4"/>
      <path d="M0,312 L0,296 C170,292 330,250 545,176 L545,312 Z" fill="var(--brand-blue)"/>
      <path d="M60,268 C220,262 370,225 545,160" fill="none" stroke="var(--brand-blue)" stroke-width="2"/>
      <path d="M0,244 C40,272 120,286 220,284 C130,296 50,296 0,282 Z" fill="var(--brand-dark)"/>
    </svg>

    <div class="brand">
      <span class="brand__dot" aria-hidden="true"></span>
      <span class="brand__name">bexil</span>
    </div>

    <div class="contact">
      <p class="contact__address">14 Harbor Lane, Milford, State 0715</p>
      <p class="contact__row contact__row--phone">
        <svg class="contact__icon" viewBox="0 0 12 12" aria-hidden="true">
          <path d="M3,1 L5,3 L4,4.5 C4.8,6 6,7.2 7.5,8 L9,7 L11,9 L9.5,11 C5,10.5 1.5,7 1,2.5 Z" fill="var(--brand-blue)"/>
        </svg>
        0451 238907
      </p>
      <p class="contact__row">
        <svg class="contact__icon" viewBox="0 0 12 12" aria-hidden="true">
          <rect x="1" y="3" width="10" height="7" rx="1" fill="var(--brand-blue)"/>
          <path d="M1.5,3.5 L6,7 L10.5,3.5" fill="none" stroke="#fff" stroke-width="1"/>
        </svg>
        info@bexil.com
      </p>
    </div>

    <div class="person">
      <p class="person__first">First Name</p>
      <p class="person__last">Last Name</p>
    </div>
  </section>

  <section class="card card--back" aria-label="Business card back">
    <div class="back-pattern" role="img" aria-label="Soft repeating brand pattern in light blue tones"></div>
    <p class="back-name">bexil</p>
  </section>

</main>
</body>
</html>
```